Business card design Needed for new logo / Construction business, home extensions and new builds

We need a business card design using our new logo files which i will attach to this project :)

We are a small construction business specialising in home extensions, new builds and property development. We are very ambitious and would appreciate professional and elegant designs for our new business card.

Very serious about using the services on MakerQuarry and recently acquired our new logo from here :)

Please get involved, i will feedback when i can as i am very busy but can respond daily, thanks

Target Market(s)

People that want to build onto their houses, new building developments or adding too their existing property

Industry/Entity Type

Construction

Contact Information for Business Card

Renwick Tolliver Construction, Lionel Ashby (Managing Director), Tel 07822254961, email - info@renwick-tolliver, www.renwick-tolliver.co.uk

Colors

Designer to choose colors to be used in the design.

Requirements
Must have
• I like a deep grey on the back please. A lot of you have provided black from and back, try mixing things up a little. The black looks cool 😎 Thanks

```html
<!DOCTYPE html>
<html lang="en">
<head>
<meta charset="utf-8">
<title>Renwick Tolliver Construction – Business Card</title>
<link href="https://fonts.googleapis.com/css2?family=Open+Sans:wght@400;600;700&display=swap" rel="stylesheet">
<style>
  :root {
    --stage: #2b2a2f;
    --card: #1e1d22;
    --card-back: #232227;
    --emboss: #161519;
    --gold: #e0a92e;
    --gold-light: #f6cf62;
    --gold-dark: #a8771a;
    --silver: #d9d9dc;
    --white: #f4f4f4;
  }
  * { box-sizing: border-box; margin: 0; padding: 0; }
  html, body { width: 1200px; height: 780px; overflow: hidden; }
  body {
    background: var(--stage);
    font-family: "Open Sans", Arial, sans-serif;
    display: flex;
    align-items: center;
    justify-content: center;
    gap: 40px;
  }
  .card {
    position: relative;
    width: 560px;
    height: 320px;
    background: var(--card);
    box-shadow: 0 10px 30px rgba(0,0,0,.45);
    overflow: hidden;
  }
  .card--back { background: var(--card-back); }
  .gold-bar {
    position: absolute;
    width: 5px;
    background: linear-gradient(90deg, var(--gold-dark), var(--gold-light) 50%, var(--gold));
  }
  .gold-bar--left { left: 14px; top: 44%; height: 44%; }
  .gold-bar--right { right: 14px; top: 12%; height: 44%; }

  /* back: embossed wordmark */
  .wordmark-emboss {
    position: absolute;
    inset: 0;
    display: flex;
    flex-direction: column;
    align-items: center;
    justify-content: center;
    gap: 14px;
    color: var(--emboss);
  }
  .wordmark-emboss .mark-square {
    width: 70px; height: 70px; background: var(--emboss);
  }
  .wordmark-emboss .wordmark-name {
    font-weight: 700; font-size: 24px; letter-spacing: 1px; text-align: center; line-height: 1.25;
  }

  /* front */
  .brand {
    position: absolute;
    left: 40px; top: 66px;
    width: 210px;
    display: flex;
    flex-direction: column;
    align-items: center;
    gap: 12px;
  }
  .brand .mark-square { width: 58px; height: 58px; background: var(--gold); }
  .brand .wordmark-name {
    color: var(--gold); font-weight: 700; font-size: 19px; letter-spacing: .5px;
    text-align: center; line-height: 1.3;
  }
  .divider {
    position: absolute; left: 272px; top: 48px; width: 1px; height: 160px;
    background: linear-gradient(180deg, rgba(255,255,255,.1), var(--silver), rgba(255,255,255,.1));
  }
  .contact { position: absolute; left: 300px; top: 50px; color: var(--white); }
  .person-name { font-size: 27px; font-weight: 700; line-height: 1.1; color: var(--silver); }
  .person-name .surname { color: var(--gold); }
  .person-title { font-size: 13px; font-weight: 600; margin-top: 2px; }
  .contact-list { list-style: none; margin-top: 22px; }
  .contact-list li {
    display: flex; align-items: center; gap: 9px; font-size: 13px; line-height: 1.75;
  }
  .contact-list svg { width: 12px; height: 12px; flex: none; }
  .address {
    position: absolute; left: 88px; bottom: 44px;
    color: var(--white); font-size: 14px; letter-spacing: .2px;
  }
</style>
</head>
<body>

  <section class="card card--back" aria-label="Card back">
    <span class="gold-bar gold-bar--left"></span>
    <span class="gold-bar gold-bar--right"></span>
    <div class="wordmark-emboss">
      <span class="mark-square"></span>
      <span class="wordmark-name">RENWICK TOLLIVER<br>CONSTRUCTION</span>
    </div>
  </section>

  <section class="card card--front" aria-label="Card front">
    <span class="gold-bar gold-bar--left"></span>
    <span class="gold-bar gold-bar--right"></span>

    <div class="brand">
      <span class="mark-square"></span>
      <span class="wordmark-name">RENWICK TOLLIVER<br>CONSTRUCTION</span>
    </div>

    <span class="divider"></span>

    <div class="contact">
      <p class="person-name">Lionel <span class="surname">Ashby</span></p>
      <p class="person-title">Managing Director</p>
      <ul class="contact-list">
        <li>
          <svg viewBox="0 0 12 12" aria-hidden="true"><path fill="#e0a92e" d="M2.5 1 4.4 1l.9 2.6-1.3 1a6.3 6.3 0 0 0 2.9 2.9l1-1.3 2.6.9v1.9c0 .6-.5 1-1 1A9.5 9.5 0 0 1 1.5 2c0-.5.4-1 1-1z"/></svg>
          0782 225 4961
        </li>
        <li>
          <svg viewBox="0 0 12 12" aria-hidden="true"><rect x="1" y="2.5" width="10" height="7" fill="#e0a92e"/><path d="M1 2.8 6 6.6 11 2.8" fill="none" stroke="#1e1d22" stroke-width="1"/></svg>
          info@renwick-tolliver.co.uk
        </li>
        <li>
          <svg viewBox="0 0 12 12" aria-hidden="true"><circle cx="6" cy="6" r="5" fill="#e0a92e"/><path d="M1 6h10M6 1c-2.5 2.8-2.5 7.2 0 10M6 1c2.5 2.8 2.5 7.2 0 10" fill="none" stroke="#1e1d22" stroke-width=".8"/></svg>
          www.renwick-tolliver.co.uk
        </li>
      </ul>
    </div>

    <p class="address">Ferncombe Road, Hartsdown Dorchester, DT4 7QL</p>
  </section>

</body>
</html>
```